Specialised investor in e-mobility and energy wants business card design

We need a business card design that fits our existing corporate design. <The look and feel must be 'sharp'/'clean', dynamic, communicate momentum, professionalism etc (as one would imagine from a firm in the financial sector). We like the idea of a reverse-side of the card that includes the logo, and the name and contact details on the other. We expect the deliverable to be whatever format might be required to be able to get cards printed directly by a service such as kelmo press. Our website is www.zub.capital

```html
<!DOCTYPE html>
<html lang="en">
<head>
<meta charset="utf-8">
<title>Zub Capital – Business Card</title>
<link href="https://fonts.googleapis.com/css2?family=Montserrat:wght@400;500;700&display=swap" rel="stylesheet">
<style>
  :root {
    --stage: #1f1f1f;
    --paper: #ffffff;
    --forest: #375a2a;
    --forest-deep: #2f4f24;
    --leaf: #7ab648;
    --ink-light: #f4f6f2;
    --ghost: #e6e9e3;
  }
  * { box-sizing: border-box; margin: 0; padding: 0; }
  html, body { width: 1200px; height: 801px; overflow: hidden; background: var(--stage); }
  body { font-family: "Montserrat", sans-serif; position: relative; }

  .card {
    position: absolute;
    top: 249px;
    width: 530px;
    height: 303px;
    border-radius: 22px;
    overflow: hidden;
  }
  .card--front { left: 50px; background: var(--paper); }
  .card--back {
    left: 620px;
    background: linear-gradient(160deg, #3f6531 0%, var(--forest) 55%, var(--forest-deep) 100%);
  }

  .card__shape { position: absolute; inset: 0; width: 100%; height: 100%; }

  .brand {
    position: absolute;
    display: flex;
    align-items: center;
    gap: 12px;
    font-weight: 500;
    letter-spacing: 0.5px;
    white-space: nowrap;
    line-height: 1;
  }
  .brand__dot { border-radius: 50%; background: var(--leaf); flex: none; }
  .card--front .brand { right: 40px; top: 44px; font-size: 38px; color: var(--forest); }
  .card--front .brand__dot { width: 15px; height: 15px; }
  .card--back .brand {
    left: 50%; top: 50%; transform: translate(-50%, -50%);
    font-size: 58px; color: var(--paper);
  }
  .card--back .brand__dot { width: 22px; height: 22px; }

  .ghost-name {
    position: absolute; left: 24px; top: 66px;
    font-size: 66px; font-weight: 700; line-height: 1;
    color: var(--ghost); letter-spacing: 2px;
  }

  .person { position: absolute; left: 30px; top: 206px; color: var(--ink-light); }
  .person__name { font-size: 18px; font-weight: 700; color: var(--leaf); line-height: 1.15; }
  .person__role { font-size: 11px; margin-top: 2px; line-height: 1.2; }
  .contact-list { list-style: none; margin-top: 8px; font-size: 10.5px; line-height: 1.5; }
  .contact-list li { display: flex; align-items: center; gap: 7px; }
  .contact-list svg { width: 10px; height: 10px; fill: var(--leaf); flex: none; }

  .divider {
    position: absolute; left: 262px; top: 222px; width: 1px; height: 56px;
    background: var(--leaf); opacity: 0.7;
  }
  .address {
    position: absolute; left: 278px; top: 224px;
    font-size: 11px; line-height: 1.5; color: var(--ink-light); font-style: normal;
  }
</style>
</head>
<body>

<section class="card card--front" aria-label="Card front">
  <svg class="card__shape" viewBox="0 0 530 303" preserveAspectRatio="none" aria-hidden="true">
    <path d="M0,186 C140,146 330,118 530,110 L530,119 C330,128 140,158 0,198 Z" fill="#7ab648"/>
    <path d="M0,198 C140,158 330,128 530,119 L530,303 L0,303 Z" fill="#375a2a"/>
  </svg>
  <div class="ghost-name" aria-hidden="true">Zub</div>
  <div class="brand"><span class="brand__dot"></span>Zub Capital</div>

  <div class="person">
    <p class="person__name">Marten Ollery</p>
    <p class="person__role">Director/Founder</p>
    <ul class="contact-list">
      <li><svg viewBox="0 0 10 10"><path d="M2 0.5 L4 2.5 L3 3.8 C3.8 5.4 4.6 6.2 6.2 7 L7.5 6 L9.5 8 L8 9.5 C4 9 1 6 0.5 2 Z"/></svg>123-480-2291</li>
      <li><svg viewBox="0 0 10 10"><path d="M0 2 H10 V8 H0 Z M0.6 2.4 L5 5.6 L9.4 2.4"/></svg>info@zub.capital</li>
      <li><svg viewBox="0 0 10 10"><circle cx="5" cy="5" r="4.5"/></svg>www.zub.capital</li>
    </ul>
  </div>

  <div class="divider"></div>
  <address class="address">
    1234 Street Name<br>Country Name AB 5748
  </address>
</section>

<section class="card card--back" aria-label="Card back">
  <div class="brand"><span class="brand__dot"></span>Zub Capital</div>
</section>

</body>
</html>
```